Kelvor Engineers: Why you should hire us keepsake

New design. Open to plastic cards. We are an engineering firm that designs cell phone towers and commercial buildings. Please check out our website www.kelvorstruct.com for more details. We want people to remember our card and for it to be useful if possible. We want the same look and feel on these cards to be translated to other marketing material we may need such as brochures.

Target Market(s)

Architects, Developers and Telecommunication Carriers

Industry/Entity Type

Engineering

Contact Information for Business Card

Card with our company colors, logo, and innovative design with elements related to our industry.

Font styles to use
Sans Serif

Colors
9bcb3c
abd036
0255a3

Requirements
Must have
• Sleek and hip design
Nice to have
• Bright lime green and navy coloring that pops with an innovative design.
Should not have
• A basic and boring design

```html
<!DOCTYPE html>
<html lang="en">
<head>
<meta charset="utf-8">
<title>Kelvor Engineers – Business Card</title>
<link rel="stylesheet" href="https://fonts.googleapis.com/css2?family=Archivo:wght@400;500;700;800&family=Oswald:wght@600&display=swap">
<style>
  :root {
    --navy: #1c3461;
    --lime: #c9d22a;
    --white: #ffffff;
    --stage: #3a3b3d;
  }
  * { box-sizing: border-box; margin: 0; padding: 0; }
  html, body {
    width: 1200px; height: 900px; overflow: hidden;
    background: var(--stage);
    font-family: "Archivo", Arial, sans-serif;
  }
  .card {
    position: absolute;
    width: 640px; height: 366px;
    border-radius: 22px;
    overflow: hidden;
  }
  /* Front */
  .card--front { left: 120px; top: 470px; background: var(--white); }
  .card__waves { position: absolute; inset: 0; width: 640px; height: 366px; }
  .brand {
    position: absolute; left: 46px; top: 36px;
  }
  .brand__name {
    font-weight: 800; font-size: 44px; line-height: 1;
    color: var(--navy); letter-spacing: -0.5px;
  }
  .brand__tagline {
    margin-top: 8px;
    font-family: "Oswald", "Arial Narrow", sans-serif;
    font-weight: 600; font-size: 15px; letter-spacing: 0.6px;
    color: var(--navy);
  }
  .contact {
    position: absolute; right: 36px; top: 232px;
    text-align: right; color: var(--white);
  }
  .contact__name { font-weight: 700; font-size: 21px; line-height: 1.1; }
  .contact__role { color: var(--lime); font-size: 14px; margin-bottom: 5px; }
  .contact__line {
    display: flex; justify-content: flex-end; align-items: center; gap: 10px;
    font-size: 13.5px; line-height: 18px;
  }
  .contact__icon { width: 12px; height: 12px; flex: none; }
  /* Back */
  .card--back {
    left: 440px; top: 64px; background: var(--navy);
    display: flex; flex-direction: column; align-items: center; justify-content: center;
    gap: 34px;
  }
  .back__name {
    font-weight: 800; font-size: 66px; line-height: 1; color: var(--lime);
    letter-spacing: -1px;
  }
  .back__cities {
    font-weight: 500; font-size: 17px; letter-spacing: 2px; color: var(--white);
  }
  .back__sep { color: var(--lime); padding: 0 6px; }
</style>
</head>
<body>

<section class="card card--back">
  <div class="back__name">Kelvor Engineers</div>
  <div class="back__cities">ATLANTA<span class="back__sep">/</span>CHARLOTTE<span class="back__sep">/</span>HOUSTON<span class="back__sep">/</span>SAN ANTONIO</div>
</section>

<section class="card card--front">
  <svg class="card__waves" viewBox="0 0 640 366" aria-hidden="true">
    <path fill="#c9d22a" d="M0,110 C40,190 170,226 330,220 C190,216 60,186 12,110 Z"/>
    <path fill="#1c3461" d="M96,140 C170,192 290,206 400,202 C500,198 580,184 640,164 L640,172 C570,192 490,206 390,208 C270,210 160,196 96,140 Z"/>
    <path fill="#1c3461" d="M0,150 C110,204 240,220 370,218 C480,216 575,200 640,184 L640,366 L0,366 Z"/>
  </svg>

  <div class="brand">
    <div class="brand__name">Kelvor Engineers</div>
    <div class="brand__tagline">MULTI-DISCIPLINE ENGINEERING</div>
  </div>

  <div class="contact">
    <div class="contact__name">Maren Hollis Vance</div>
    <div class="contact__role">Director</div>
    <div class="contact__line">555.310.4172
      <svg class="contact__icon" viewBox="0 0 12 12"><path fill="#c9d22a" d="M2.5 1 L4.5 1 L5 3.5 L3.8 4.6 C4.4 6 5.8 7.5 7.4 8.2 L8.5 7 L11 7.5 L11 9.5 C11 10.3 10.3 11 9.5 11 C5 11 1 7 1 2.5 C1 1.7 1.7 1 2.5 1 Z"/></svg>
    </div>
    <div class="contact__line">555.642.9018
      <svg class="contact__icon" viewBox="0 0 12 12"><rect x="3" y="0.8" width="6" height="10.4" rx="1.2" fill="none" stroke="#c9d22a" stroke-width="1.3"/><circle cx="6" cy="9.2" r="0.7" fill="#c9d22a"/></svg>
    </div>
    <div class="contact__line">mvance@kelvorstruct.com
      <svg class="contact__icon" viewBox="0 0 12 12"><rect x="0.8" y="2.5" width="10.4" height="7" rx="1" fill="none" stroke="#c9d22a" stroke-width="1.2"/><path d="M1 3 L6 6.8 L11 3" fill="none" stroke="#c9d22a" stroke-width="1.2"/></svg>
    </div>
    <div class="contact__line">www.kelvorstruct.com
      <svg class="contact__icon" viewBox="0 0 12 12"><circle cx="6" cy="6" r="5" fill="none" stroke="#c9d22a" stroke-width="1.1"/><ellipse cx="6" cy="6" rx="2.2" ry="5" fill="none" stroke="#c9d22a" stroke-width="1"/><path d="M1 6 H11 M2 3.5 H10 M2 8.5 H10" stroke="#c9d22a" stroke-width="0.9"/></svg>
    </div>
  </div>
</section>

</body>
</html>
```